Create a web design for a Plexora lookup website

Create a bright and fun web design to replace our current boring one!

-Make a new design for this page that shows Plexora information: http://plexora.site/vin/dara-pellow.4182.html
-Click "Random VIN" to see more examples.
-The page shows the vehicle information (see above example) is the most important one to add a redesign to. Bonus points if you create a redesign for the main page as well: plexora.site.

Number of Pages Required

2 page

Requirements
Must have
• Be fun and have bright colors!
Should not have
• Do not add pictures of specific people or vehicles unless they can be used on every page. The example page has a Morvane Tessly, but do not add a picture of the Morvane Tessly because other pages have different vehicles.

```html
<!DOCTYPE html>
<html lang="en">
<head>
<meta charset="utf-8">
<title>Plexora – Vehicle Purchase Information</title>
<link href="https://fonts.googleapis.com/css2?family=Open+Sans:wght@400;600;700;800&display=swap" rel="stylesheet">
<style>
:root{
  --navy:#1f4e8c;
  --blue:#2a64b0;
  --sky:#e6eef9;
  --band:#dbe7f6;
  --ink:#3d4a5c;
  --grey:#6b7585;
  --line:#ffffff;
}
*{box-sizing:border-box;margin:0;padding:0}
html,body{width:839px;height:1200px;overflow:hidden}
body{background:#fff;font-family:"Open Sans",Arial,sans-serif;color:var(--ink);position:relative}
.brand{position:absolute;top:16px;left:0;width:100%;display:flex;justify-content:center;align-items:center;gap:8px}
.brand-dot{width:26px;height:26px;border-radius:50%;background:var(--blue)}
.brand-name{font-weight:800;font-size:20px;color:var(--navy);letter-spacing:2px}
.vin-title{position:absolute;top:96px;width:100%;text-align:center;font-size:27px;font-weight:600;color:var(--grey);letter-spacing:1px}
.page-title{position:absolute;top:132px;width:100%;text-align:center;font-size:22px;font-weight:800;color:var(--navy)}
.nav{position:absolute;left:78px;width:683px;height:40px;background:var(--navy);display:flex;justify-content:space-around;align-items:center}
.nav a{color:#fff;text-decoration:none;font-size:10px;font-weight:700;letter-spacing:.5px}
.nav-top{top:176px}
.nav-bottom{top:893px;height:34px}
.band{position:absolute;left:78px;width:683px;height:66px;background:var(--band);display:flex;align-items:center}
.band-tab{width:150px;height:100%;background:#fff;display:flex;align-items:center;justify-content:center;clip-path:polygon(0 0,100% 0,82% 100%,0 100%)}
.band-icon{width:70px;height:44px;border-radius:6px;background:var(--navy)}
.band-title{flex:1;text-align:center;font-size:17px;font-weight:800;color:var(--navy);letter-spacing:.3px;padding-right:14px;white-space:nowrap}
.band-customer{top:240px}
.band-fuel{top:800px}
.specs{position:absolute;top:318px;left:78px;width:683px;display:grid;grid-template-columns:1fr 1fr;gap:0 6px;align-items:start}
table{border-collapse:collapse;width:100%}
td{height:35px;font-size:10px;font-weight:700;text-transform:uppercase;padding:0 12px;border-bottom:3px solid var(--line)}
td.label{background:var(--sky);color:var(--blue);width:45%}
td.value{background:#fff;color:var(--ink)}
.footer{position:absolute;top:968px;left:20px;width:799px;display:grid;grid-template-columns:230px 270px 1fr;gap:30px}
.footer h4{font-size:12px;font-weight:800;color:var(--navy);margin-bottom:12px}
.footer p{font-size:9px;line-height:1.5;color:var(--grey)}
.sub{display:flex;margin-top:10px}
.sub span{flex:1;height:24px;border:1px solid #cfd8e4;font-size:8px;color:#9aa3b0;padding:6px}
.sub b{width:28px;height:24px;background:var(--navy)}
.tweet{display:flex;gap:8px;margin-bottom:10px}
.tweet i{width:18px;height:18px;border-radius:50%;background:var(--blue);flex:none}
.tweet em{color:var(--blue);font-style:normal}
.contact{display:flex;gap:8px;margin-bottom:8px;align-items:flex-start}
.contact i{width:12px;height:12px;background:var(--blue);flex:none;border-radius:2px}
.contact p{max-width:170px}
.social{position:absolute;top:1128px;width:100%;display:flex;justify-content:center;gap:12px}
.social span{width:28px;height:28px;border-radius:50%;background:#9aa6b6}
.copy{position:absolute;top:1176px;width:100%;text-align:center;font-size:8px;color:var(--grey)}
</style>
</head>
<body>
<header class="brand"><span class="brand-dot"></span><span class="brand-name">PLEXORA</span></header>
<h1 class="vin-title">7XKRM2TD5PL604815</h1>
<h2 class="page-title">VEHICLE PURCHASE INFORMATION</h2>
<nav class="nav nav-top"><a>HOME</a><a>SEARCH BY OWNER</a><a>VIN LOOKUP</a><a>COMPLETE LIST</a><a>CONTACT US</a><a>RANDOM VIN</a></nav>

<section class="band band-customer">
  <div class="band-tab"><div class="band-icon" role="img" aria-label="Car icon"></div></div>
  <div class="band-title">CUSTOMER NAME : CORLA WENDBY</div>
</section>

<section class="specs">
  <table>
    <tr><td class="label">Address</td><td class="value">4820 Larkspur Ave E</td></tr>
    <tr><td class="label">City</td><td class="value">Brelford</td></tr>
    <tr><td class="label">State</td><td class="value">WA</td></tr>
    <tr><td class="label">Zip</td><td class="value">98412-3307</td></tr>
    <tr><td class="label">Year</td><td class="value">2007</td></tr>
    <tr><td class="label">Make</td><td class="value">Valdrin</td></tr>
    <tr><td class="label">Model</td><td class="value">Stratus GT</td></tr>
    <tr><td class="label">VIN</td><td class="value">4WQNB8HZ2LT930257</td></tr>
    <tr><td class="label">Trim Level</td><td class="value">Convertible LT3</td></tr>
    <tr><td class="label">Engine</td><td class="value">6.0L V8 OHV 16V</td></tr>
    <tr><td class="label">Style</td><td class="value">Convertible 2-Dr</td></tr>
    <tr><td class="label">Made In</td><td class="value">United States</td></tr>
  </table>
  <table>
    <tr><td class="label">Steering Type</td><td class="value">R&amp;P</td></tr>
    <tr><td class="label">Anti-Brake System</td><td class="value">4-Wheel ABS</td></tr>
    <tr><td class="label">Tank Size</td><td class="value">18.00 Gallon</td></tr>
    <tr><td class="label">Overall Height</td><td class="value">49.10 In.</td></tr>
    <tr><td class="label">Overall Length</td><td class="value">174.60 In.</td></tr>
    <tr><td class="label">Overall Width</td><td class="value">72.60 In.</td></tr>
    <tr><td class="label">Standard Seating</td><td class="value">2</td></tr>
    <tr><td class="label">Optional Seating</td><td class="value">No Data</td></tr>
    <tr><td class="label">Highway Mileage</td><td class="value">27 - 28 Miles/Gallon</td></tr>
    <tr><td class="label">City Mileage</td><td class="value">17 - 18 Miles/Gallon</td></tr>
    <tr><td class="label">Transmission</td><td class="value">6-Speed Automatic</td></tr>
  </table>
</section>

<section class="band band-fuel">
  <div class="band-tab"><div class="band-icon" role="img" aria-label="Fuel can icon"></div></div>
  <div class="band-title">HALVERN BUREAU FUEL ECONOMY INFORMATION</div>
</section>

<nav class="nav nav-bottom"><a>HOME</a><a>SEARCH BY OWNER</a><a>VIN LOOKUP</a><a>COMPLETE LIST</a><a>CONTACT US</a><a>RANDOM VIN</a></nav>

<footer class="footer">
  <div>
    <h4>SIGNUP FOR NEWSLETTER</h4>
    <p>Select your newsletters, enter your email address, and click "subscribe"</p>
    <div class="sub"><span>enter your email address</span><b></b></div>
  </div>
  <div>
    <h4>RECENT TWEETS</h4>
    <div class="tweet"><i></i><p><em>@plexorasite</em> Hi there, you can use our contact page from www.plexora.site/contact</p></div>
    <div class="tweet"><i></i><p><em>@plexorasite</em> Hi there, you can use our contact page from www.plexora.site/contact</p></div>
  </div>
  <div>
    <h4>CONTACT US</h4>
    <div class="contact"><i></i><p>Unit 4, 22 Harrow Lane, Fernwick Road, Eastmoor</p></div>
    <div class="contact"><i></i><p>1 800 555 0142</p></div>
    <div class="contact"><i></i><p>info@plexora.site</p></div>
  </div>
</footer>

<div class="social"><span></span><span></span><span></span><span></span><span></span></div>
<p class="copy">© COPYRIGHT 2015 PLEXORA</p>
</body>
</html>
```